Business Card Design - Property Management & Real Estate Services

I need a business card design for my company that I can print ZEPLA Cards. The company is called Brindle Management Company. It is a property management and real estate company. The design has to be clean and modern. I need two versions. One for my employee and one for me. However, the design will be the same, just different text. You can get a feel for the company by looking at our website at www.brindlemanagement.example.

Industry/Entity Type

Property Management

Contact Information for Business Card

I will be using ZEPLA.com to print my cards. I will most likely use the rounded edges card. I need two versions, however, they will be the same design. I need one for me and my employee.

Colors
3276b5
33a6d7

Requirements
Must have
• Company Logo
• Name of person
• Property Management & Real Estate Service
• Phone
• Email
• Website
• Address
• A space to place a QR code

```html
<!DOCTYPE html>
<html lang="en">
<head>
<meta charset="utf-8">
<title>Brindle Management – Business Card</title>
<link rel="stylesheet" href="https://fonts.googleapis.com/css2?family=Montserrat:wght@500&family=Roboto:wght@400;500&family=Saira+Condensed:wght@700&display=swap">
<style>
  :root {
    --bg: #c9c9cb;
    --card: #ffffff;
    --navy: #1b4f9b;
    --blue: #3276b5;
    --light-blue: #6f9ad0;
    --ink: #2a2a2a;
    --on-blue: #ffffff;
    --on-blue-soft: #dce6f4;
  }
  * { margin: 0; padding: 0; box-sizing: border-box; }
  html, body { width: 1200px; height: 852px; overflow: hidden; }
  body { background: var(--bg); position: relative; font-family: "Roboto", sans-serif; }

  .card {
    position: absolute;
    width: 500px;
    height: 286px;
    border-radius: 14px;
    overflow: hidden;
    background: var(--card);
    box-shadow: 0 6px 18px rgba(0,0,0,0.18);
  }
  .card--front { left: 70px; top: 150px; }
  .card--back  { left: 630px; top: 410px; }

  .wordmark {
    position: absolute;
    text-align: center;
    font-family: "Montserrat", sans-serif;
    font-weight: 500;
    color: var(--navy);
    line-height: 1;
  }
  .wordmark__name { display: block; font-size: 40px; letter-spacing: 2px; }
  .wordmark__sub  { display: block; font-size: 12px; letter-spacing: 8px; margin-top: 8px; }

  .card--front .wordmark { left: 0; right: 0; top: 86px; }

  .tagline {
    position: absolute; left: 0; right: 0; top: 160px;
    text-align: center;
    font-size: 9px; font-weight: 500; letter-spacing: 2px;
    color: var(--blue);
  }

  .front-web {
    position: absolute; left: 0; right: 0; top: 196px;
    display: flex; justify-content: center; align-items: center; gap: 12px;
    font-size: 12px; color: var(--ink);
  }
  .front-web__rule { width: 40px; height: 1.5px; background: var(--blue); }

  .front-band { position: absolute; left: 0; right: 0; bottom: 0; height: 10px; display: flex; }
  .front-band__light { width: 42%; background: var(--light-blue); }
  .front-band__dark  { flex: 1; background: var(--navy); }

  .back-shape { position: absolute; inset: 0; }

  .card--back .wordmark { left: 285px; width: 200px; top: 90px; }
  .card--back .wordmark__name { font-size: 34px; }
  .card--back .wordmark__sub { font-size: 10px; letter-spacing: 6px; }

  .qr-space {
    position: absolute; left: 418px; top: 168px;
    width: 58px; height: 58px;
    border: 1.5px dashed var(--light-blue);
    border-radius: 4px;
  }

  .person { position: absolute; left: 28px; top: 36px; color: var(--on-blue); }
  .person__name { font-family: "Saira Condensed", sans-serif; font-weight: 700; font-size: 21px; letter-spacing: 0.3px; }
  .person__role { font-size: 12px; color: var(--on-blue-soft); margin-top: 2px; padding-left: 12px; }

  .contacts { position: absolute; left: 28px; bottom: 28px; list-style: none; color: var(--on-blue); font-size: 12px; }
  .contacts li { display: flex; align-items: center; gap: 8px; height: 18px; }
  .contacts svg { width: 11px; height: 11px; flex: none; fill: var(--on-blue); }
  .contacts .no-icon { padding-left: 19px; }
</style>
</head>
<body>

  <section class="card card--front" aria-label="Card front">
    <div class="wordmark">
      <span class="wordmark__name">BRINDLE</span>
      <span class="wordmark__sub">MANAGEMENT</span>
    </div>
    <p class="tagline">PROPERTY MANAGEMENT &amp; REAL ESTATE SERVICES</p>
    <div class="front-web">
      <span class="front-web__rule"></span>
      <span>www.brindlemanagement.example</span>
      <span class="front-web__rule"></span>
    </div>
    <div class="front-band">
      <span class="front-band__light"></span>
      <span class="front-band__dark"></span>
    </div>
  </section>

  <section class="card card--back" aria-label="Card back">
    <svg class="back-shape" viewBox="0 0 500 286" preserveAspectRatio="none" aria-hidden="true">
      <path d="M0 0 H268 C262 120 300 230 500 286 H0 Z" fill="var(--light-blue)"/>
      <path d="M0 0 H255 C248 125 290 235 470 286 H0 Z" fill="var(--navy)"/>
    </svg>

    <div class="person">
      <p class="person__name">Marcos T. Ibarra</p>
      <p class="person__role">Founder</p>
    </div>

    <ul class="contacts">
      <li class="no-icon">(305) 555-0142</li>
      <li>
        <svg viewBox="0 0 12 12"><path d="M2 1h2.5l1 3-1.5 1a6 6 0 0 0 3 3l1-1.5 3 1V10a1 1 0 0 1-1 1A9 9 0 0 1 1 2a1 1 0 0 1 1-1z"/></svg>
        marcos@brindlemanagement.example
      </li>
      <li>
        <svg viewBox="0 0 12 12"><path d="M0 2.5h12v7H0z M0.8 3l5.2 3.6L11.2 3" fill="none" stroke="#fff" stroke-width="1"/></svg>
        www.brindlemanagement.example
      </li>
      <li>
        <svg viewBox="0 0 12 12"><circle cx="6" cy="6" r="5.5"/></svg>
        480 Harbor Ave #210 Miami, FL 33100
      </li>
    </ul>

    <div class="wordmark">
      <span class="wordmark__name">BRINDLE</span>
      <span class="wordmark__sub">MANAGEMENT</span>
    </div>

    <div class="qr-space" role="img" aria-label="Space reserved for a QR code"></div>
  </section>

</body>
</html>
```